Colin Vardek Business card

Hey there, I’m hoping to have a business card designed. I’m in Real estate and just switched to a new Brokerage called: The Harbourline Property Group

The back could just be the company name maybe or whatever looks good!

I’ve attached some logos of our company and some cards my buddy had done up.

On the card:
Colin Vardek
colinvardek@mailora.com
587-412-9065
colinvardek.ca

Target Market(s)

Home buyers and sellers

Industry/Entity Type

Real Estate

Contact Information for Business Card

just looking for a cool and modern design with my picture on it. I like the idea of Black and red being used.

Requirements
Must have
• all the details provided. I'm open to anything. Just want a professional looking card.

```html
<!DOCTYPE html>
<html lang="en">
<head>
<meta charset="utf-8">
<title>Colin Vardek Business Card</title>
<link rel="stylesheet" href="https://fonts.googleapis.com/css2?family=Poppins:wght@300;400;600;700&display=swap">
<style>
  :root {
    --backdrop: #232325;
    --card: #202024;
    --red: #d8233a;
    --white: #f4f4f4;
    --muted: #dcdcdc;
  }
  * { box-sizing: border-box; margin: 0; padding: 0; }
  html, body { width: 1200px; height: 711px; overflow: hidden; background: var(--backdrop); }
  body { font-family: "Poppins", sans-serif; position: relative; }

  .card {
    position: absolute;
    top: 60px;
    width: 330px;
    height: 590px;
    background: var(--card);
    border: 2px solid var(--red);
    box-shadow: 0 14px 30px rgba(0,0,0,.55);
    overflow: hidden;
  }
  .card--back { left: 250px; border-radius: 165px 0 165px 0; }
  .card--front { left: 620px; border-radius: 0 165px 0 165px; }

  /* Back */
  .back-brand {
    position: absolute;
    left: 50%;
    top: 50%;
    transform: translate(-50%, -50%) rotate(-90deg);
    display: flex;
    align-items: center;
    gap: 14px;
    white-space: nowrap;
  }
  .back-brand__mark { width: 18px; height: 18px; background: var(--red); }
  .back-brand__name { font-weight: 700; font-size: 30px; color: var(--red); letter-spacing: .5px; }

  /* Front */
  .front-brand {
    position: absolute;
    top: 52px;
    left: 0;
    right: 0;
    text-align: center;
    font-weight: 700;
    font-size: 15px;
    color: var(--white);
    letter-spacing: .4px;
  }
  .portrait {
    position: absolute;
    top: 170px;
    left: 50%;
    transform: translateX(-50%);
    width: 150px;
    height: 150px;
    border-radius: 50%;
    border: 3px solid var(--red);
    background: radial-gradient(circle at 50% 40%, #ffffff 0%, #f2f2f2 55%, #2a2a2e 56%, #1c1c20 100%);
  }
  .agent-name {
    position: absolute;
    top: 345px;
    left: 0;
    right: 0;
    text-align: center;
    font-size: 30px;
    line-height: 1.1;
  }
  .agent-name__first { color: var(--red); font-weight: 700; }
  .agent-name__last { color: var(--white); font-weight: 300; }

  .contact-list {
    position: absolute;
    top: 415px;
    left: 58px;
    list-style: none;
  }
  .contact-list__item {
    display: flex;
    align-items: center;
    gap: 10px;
    font-size: 13px;
    font-weight: 300;
    color: var(--muted);
    margin-bottom: 10px;
  }
  .contact-list__icon { width: 14px; height: 14px; flex: none; }
</style>
</head>
<body>

  <section class="card card--back" aria-label="Card back">
    <div class="back-brand">
      <span class="back-brand__mark"></span>
      <span class="back-brand__name">The Harbourline Property Group</span>
    </div>
  </section>

  <section class="card card--front" aria-label="Card front">
    <p class="front-brand">The Harbourline Property Group</p>

    <div class="portrait" role="img" aria-label="Portrait photo of Colin Vardek"></div>

    <h1 class="agent-name">
      <span class="agent-name__first">Colin</span>
      <span class="agent-name__last">Vardek</span>
    </h1>

    <ul class="contact-list">
      <li class="contact-list__item">
        <svg class="contact-list__icon" viewBox="0 0 24 24" aria-hidden="true">
          <path fill="#d8233a" d="M6.6 10.8a15.1 15.1 0 0 0 6.6 6.6l2.2-2.2a1 1 0 0 1 1-.25 11.4 11.4 0 0 0 3.6.57 1 1 0 0 1 1 1V20a1 1 0 0 1-1 1A17 17 0 0 1 3 4a1 1 0 0 1 1-1h3.5a1 1 0 0 1 1 1c0 1.25.2 2.45.57 3.57a1 1 0 0 1-.25 1z"/>
        </svg>
        587-412-9065
      </li>
      <li class="contact-list__item">
        <svg class="contact-list__icon" viewBox="0 0 24 24" aria-hidden="true">
          <circle cx="12" cy="12" r="9.5" fill="none" stroke="#d8233a" stroke-width="2"/>
          <ellipse cx="12" cy="12" rx="4" ry="9.5" fill="none" stroke="#d8233a" stroke-width="2"/>
          <path d="M2.5 12h19" stroke="#d8233a" stroke-width="2"/>
        </svg>
        www.colinvardek.ca
      </li>
      <li class="contact-list__item">
        <svg class="contact-list__icon" viewBox="0 0 24 24" aria-hidden="true">
          <rect x="2" y="5" width="20" height="14" rx="2" fill="#d8233a"/>
          <path d="M3 6l9 7 9-7" fill="none" stroke="#202024" stroke-width="2"/>
        </svg>
        colinvardek@mailora.com
      </li>
    </ul>
  </section>

</body>
</html>
```